Doors for Chiropractic Office

In my chiropractic office I have 6 treatment rooms and 2 massage rooms. The entire office is going through a remodel. The overall color scheme is very earth tones but in order to add some color, the 6 doors to the treatment rooms will all be a separate color (Red, Blue, Yellow, Green etc)
I need to number each room 1,2,3,4,5,6 and the 2 massage rooms. I had the idea of putting a giant number on each door, so I am looking for some graphic ideas for that project.
The rooms are located with 4 on each side of a long hallway with the 2 massage rooms at the end.
The purpose of numbering each door is to direct the patients where to go.
I have uploaded pictures of the hall way. Pardon the dust since we are under construction but hopefully it gives you an idea of the layout. The door colors will change as stated above.

Requirements
Nice to have
• I would like to see someone come up with a design where each number for the doors are created out of vertebrae's.

```html
<!DOCTYPE html>
<html lang="en">
<head>
<meta charset="utf-8">
<title>Treatment Room Doors</title>
<link rel="stylesheet" href="https://fonts.googleapis.com/css2?family=Roboto+Slab:wght@900&display=swap">
<style>
  :root {
    --wall: #5e5e5e;
    --ink: #ffffff;
    --door-one: #ffcc00;
    --door-two: #f2650a;
    --door-three: #f50000;
    --door-four: #ee2a7e;
    --door-five: #123684;
    --door-six: #05ae9b;
  }
  html, body {
    margin: 0;
    padding: 0;
    width: 1200px;
    height: 1200px;
    overflow: hidden;
    background: var(--wall);
  }
  .door-set {
    position: relative;
    width: 1200px;
    height: 1200px;
  }
  .door-panel {
    position: absolute;
    width: 226px;
    height: 502px;
    display: block;
  }
  .door-panel--one   { left: 189px; top: 64px;  }
  .door-panel--two   { left: 493px; top: 64px;  }
  .door-panel--three { left: 787px; top: 64px;  }
  .door-panel--four  { left: 189px; top: 640px; }
  .door-panel--five  { left: 493px; top: 640px; }
  .door-panel--six   { left: 787px; top: 640px; }
  .door-number {
    font-family: "Roboto Slab", "Rockwell", Georgia, serif;
    font-weight: 900;
    font-size: 142px;
  }
  .door-number__word { fill: var(--ink); }
  .door-pattern { fill: url(#pattern-tint); }
</style>
</head>
<body>
<svg width="0" height="0" style="position:absolute" aria-hidden="true">
  <defs>
    <linearGradient id="pattern-tint" x1="0" y1="0" x2="1" y2="0">
      <stop offset="0" stop-color="#ffffff" stop-opacity="0"/>
      <stop offset="1" stop-color="#ffffff" stop-opacity="0.14"/>
    </linearGradient>
  </defs>
</svg>
<main class="door-set">

  <svg class="door-panel door-panel--one" viewBox="0 0 226 502" aria-label="Room one">
    <rect width="226" height="502" fill="var(--door-one)"/>
    <rect class="door-pattern" x="30" y="198" width="96" height="304" role="img" aria-label="Faint outline lettering pattern"/>
    <g class="door-number" transform="translate(220 502) rotate(-90)">
      <text class="door-number__word" x="0" y="0" textLength="304" lengthAdjust="spacingAndGlyphs">ONE</text>
    </g>
  </svg>

  <svg class="door-panel door-panel--two" viewBox="0 0 226 502" aria-label="Room two">
    <rect width="226" height="502" fill="var(--door-two)"/>
    <rect class="door-pattern" x="30" y="178" width="96" height="324" role="img" aria-label="Faint outline lettering pattern"/>
    <g class="door-number" transform="translate(220 502) rotate(-90)">
      <text class="door-number__word" x="0" y="0" textLength="323" lengthAdjust="spacingAndGlyphs">TWO</text>
    </g>
  </svg>

  <svg class="door-panel door-panel--three" viewBox="0 0 226 502" aria-label="Room three">
    <rect width="226" height="502" fill="var(--door-three)"/>
    <rect class="door-pattern" x="30" y="46" width="96" height="456" role="img" aria-label="Faint outline lettering pattern"/>
    <g class="door-number" transform="translate(220 502) rotate(-90)">
      <text class="door-number__word" x="0" y="0" textLength="456" lengthAdjust="spacingAndGlyphs">THREE</text>
    </g>
  </svg>

  <svg class="door-panel door-panel--four" viewBox="0 0 226 502" aria-label="Room four">
    <rect width="226" height="502" fill="var(--door-four)"/>
    <rect class="door-pattern" x="30" y="115" width="96" height="387" role="img" aria-label="Faint outline lettering pattern"/>
    <g class="door-number" transform="translate(220 502) rotate(-90)">
      <text class="door-number__word" x="0" y="0" textLength="387" lengthAdjust="spacingAndGlyphs">FOUR</text>
    </g>
  </svg>

  <svg class="door-panel door-panel--five" viewBox="0 0 226 502" aria-label="Room five">
    <rect width="226" height="502" fill="var(--door-five)"/>
    <rect class="door-pattern" x="30" y="187" width="96" height="315" role="img" aria-label="Faint outline lettering pattern"/>
    <g class="door-number" transform="translate(220 502) rotate(-90)">
      <text class="door-number__word" x="0" y="0" textLength="315" lengthAdjust="spacingAndGlyphs">FIVE</text>
    </g>
  </svg>

  <svg class="door-panel door-panel--six" viewBox="0 0 226 502" aria-label="Room six">
    <rect width="226" height="502" fill="var(--door-six)"/>
    <rect class="door-pattern" x="30" y="278" width="96" height="222" role="img" aria-label="Faint outline lettering pattern"/>
    <g class="door-number" transform="translate(220 500) rotate(-90)">
      <text class="door-number__word" x="0" y="0" textLength="222" lengthAdjust="spacingAndGlyphs">SIX</text>
    </g>
  </svg>

</main>
</body>
</html>
```